Call Center In Need of Website Design

We are a call center that provides inbound and outbound calling & marketing services for eCommerce store. We would like to see a fun, creative, playful design that is simple.

Here are some sample design sites we like;
- https://www.velmoreline.com/
- https://pindrask.io/
- https://www.glimbertic.com/live-chat-software/
- https://www.zavrolin.com/

Here are some competitor sites;
- https://www.ostrevaglinks.com/
- https://www.helpkestrel.com/

I have attached website content for your use.

Target Market(s)

eCommerce

Coding

Coded - Design and coding required

Number of Pages Required

5+ page

Font styles to use
Sans Serif

Colors

Designer to choose colors to be used in the design.

Requirements
Must have
• Must have designs for the following 5 separate pages;
• 1. Home (landing)
• - This will be were the design style really needs to show.
• - Just needs to touch on key services
• - CTA
• 2. About Us
• - Basic page for about me paragraph
• 3. Services
• - List of services with icons
• - Click on service type to expand details or hover over service icon to view popup bubble with details about that service
• 4. Pricing
• - Option to bundle 1(one) digital service plan and 1(one) call center service plan
• - Bundling adds 10% monthly discount to over all price
• - Customer does NOT have to bundle
• - FAQ
• 5. Contact Us
• - Include a capture form (name, company name, email, phone, message)
• - Contact info
• - Business hours
• When customer purchases their desired plan, then they are taken to a page where they must schedule a call with an account rep.
Nice to have
• home page animations
Should not have
• All information on Home/Landing page.

```html
<!DOCTYPE html>
<html lang="en">
<head>
<meta charset="UTF-8">
<title>Novaline – Omnichannel Customer Care</title>
<link rel="stylesheet" href="https://fonts.googleapis.com/css2?family=Poppins:wght@300;400;500;600;700&display=swap">
<style>
  :root {
    --hero-deep: #14506b;
    --hero-mid: #1f7390;
    --hero-light: #3a98ad;
    --accent: #43b59b;
    --accent-dark: #2f8f7b;
    --mint: #63c6ad;
    --mint-light: #e9f6f3;
    --faq-band: #edf7f6;
    --ink: #23475a;
    --muted: #7d8f98;
    --line: #dfe7ea;
    --white: #ffffff;
  }
  * { box-sizing: border-box; margin: 0; padding: 0; }
  html, body { width: 769px; height: 1200px; overflow: hidden; }
  body { font-family: "Poppins", sans-serif; color: var(--ink); background: var(--white); position: relative; }

  /* Hero */
  .hero { position: absolute; top: 0; left: 0; width: 769px; height: 480px;
    background: linear-gradient(160deg, var(--hero-mid) 0%, var(--hero-deep) 70%); overflow: hidden; }
  .hero-art { position: absolute; right: 0; top: 0; width: 400px; height: 430px;
    background: radial-gradient(circle at 70% 40%, #6fb6c8 0%, #2d7f98 45%, rgba(20,80,107,0) 75%); }
  .hero-watermark { position: absolute; left: 478px; top: 110px; transform: rotate(-90deg); transform-origin: left top;
    font-size: 50px; font-weight: 300; letter-spacing: 10px; color: rgba(255,255,255,0.14); white-space: nowrap; translate: 0 240px; }
  .site-nav { position: absolute; top: 28px; left: 40px; right: 40px; display: flex; align-items: center; justify-content: space-between; }
  .brand { display: flex; align-items: center; gap: 10px; color: var(--white); font-size: 24px; font-weight: 500; letter-spacing: 5px; }
  .brand-dot { width: 22px; height: 22px; border-radius: 50%; background: var(--accent); }
  .nav-links { display: flex; gap: 18px; list-style: none; }
  .nav-links li { color: var(--white); font-size: 8px; font-weight: 500; letter-spacing: 0.5px; text-transform: uppercase; }
  .nav-links li.is-active { border-bottom: 1px solid var(--white); }
  .hero-copy { position: absolute; left: 40px; top: 240px; color: var(--white); }
  .hero-title { font-size: 24px; font-weight: 600; line-height: 1.2; }
  .hero-sub { font-size: 16px; font-weight: 400; margin-top: 4px; }
  .hero-actions { display: flex; gap: 22px; margin-top: 70px; }
  .hero-actions a { color: var(--white); font-size: 8px; font-weight: 600; text-decoration: none; text-transform: uppercase;
    border-bottom: 1px solid var(--white); padding-bottom: 2px; }
  .hero-wave { position: absolute; left: 0; bottom: 0; width: 769px; height: 120px; }

  /* What we do */
  .services { position: absolute; top: 495px; left: 0; width: 769px; height: 120px; }
  .service-card { position: absolute; top: 0; width: 122px; height: 100px; background: var(--white);
    box-shadow: 0 4px 14px rgba(20,80,107,0.15); }
  .service-card .icon-box { height: 58px; background: var(--hero-mid); display: flex; align-items: center; justify-content: center; }
  .service-card.alt .icon-box { background: var(--white); border-bottom: 1px solid var(--line); }
  .service-card h3 { font-size: 8px; font-weight: 600; margin: 8px 10px 2px; }
  .service-card p { font-size: 6px; color: var(--muted); margin: 0 10px; }
  .card-digital { left: 115px; }
  .card-call { left: 245px; }
  .what-we-do { position: absolute; left: 385px; top: 4px; width: 270px; }
  .what-we-do h2 { font-size: 13px; font-weight: 600; margin-bottom: 8px; }
  .what-we-do p { font-size: 7px; line-height: 1.7; color: var(--muted); }
  .btn-more { display: inline-block; margin-top: 12px; background: var(--accent); color: var(--white); font-size: 7px;
    padding: 6px 16px; border-radius: 3px; }

  /* FAQ */
  .faq { position: absolute; top: 610px; left: 0; width: 769px; height: 345px; background: var(--faq-band); }
  .faq h2 { text-align: center; margin-top: 38px; font-size: 20px; font-weight: 500; color: var(--hero-deep); }
  .faq-rule { width: 50px; height: 2px; background: var(--accent); margin: 6px auto; }
  .faq-sub { text-align: center; font-size: 7px; color: var(--muted); }
  .faq-slider { position: absolute; left: 150px; top: 110px; width: 460px; height: 140px; background: var(--white);
    border-top: 3px solid var(--accent); box-shadow: 0 4px 16px rgba(20,80,107,0.12); }
  .faq-answer { position: absolute; left: 24px; top: 18px; width: 210px; font-size: 7px; line-height: 1.7; color: var(--muted); }
  .faq-question { position: absolute; left: 24px; top: 108px; font-size: 8px; font-weight: 600; color: var(--hero-deep); }
  .faq-brand { position: absolute; right: 40px; top: 52px; display: flex; align-items: center; gap: 8px;
    font-size: 22px; font-weight: 500; letter-spacing: 4px; color: var(--hero-deep); }
  .faq-brand .brand-dot { width: 20px; height: 20px; }
  .faq-arrow { position: absolute; top: 182px; width: 16px; height: 10px; }
  .faq-arrow.prev { left: 150px; }
  .faq-arrow.next { left: 594px; }
  .faq-dots { position: absolute; top: 184px; left: 0; width: 769px; display: flex; justify-content: center; gap: 5px; }
  .faq-dots span { width: 5px; height: 5px; border-radius: 50%; background: #b9cdd3; }
  .faq-dots span.is-active { background: var(--hero-deep); }
  .rocket-art { position: absolute; left: 630px; top: 130px; width: 100px; height: 240px;
    background: linear-gradient(180deg, rgba(99,198,173,0.35), rgba(99,198,173,0.8)); border-radius: 50px 50px 10px 10px; z-index: 2; }

  /* Call back */
  .callback { position: absolute; top: 955px; left: 0; width: 769px; height: 175px; background: var(--mint); }
  .contact-box { position: absolute; left: 115px; top: -10px; width: 185px; height: 175px; background: var(--accent-dark); color: var(--white); padding: 20px 18px; }
  .contact-box h3 { font-size: 10px; font-weight: 600; margin-bottom: 14px; }
  .contact-box li { list-style: none; display: flex; align-items: center; gap: 8px; font-size: 7px; margin-bottom: 12px; }
  .callback-form { position: absolute; left: 318px; top: 18px; width: 290px; }
  .callback-form h2 { font-size: 18px; font-weight: 500; color: var(--white); margin-bottom: 14px; }
  .field-grid { display: grid; grid-template-columns: 1fr 1fr; gap: 8px; }
  .field { height: 20px; border: 1px solid rgba(255,255,255,0.7); font-size: 7px; color: var(--white); padding: 5px 8px; }
  .btn-submit { display: inline-block; margin-top: 14px; background: var(--accent-dark); color: var(--white); font-size: 7px; padding: 7px 16px; }

  /* Footer */
  .site-footer { position: absolute; top: 1130px; left: 0; width: 769px; height: 70px; background: var(--white);
    display: flex; align-items: center; justify-content: space-between; padding: 0 40px; }
  .site-footer p { font-size: 6px; color: var(--muted); width: 90px; }
  .footer-links { display: flex; gap: 20px; list-style: none; margin-right: 180px; }
  .footer-links li { font-size: 7px; color: var(--muted); }
  .footer-links li.is-active { color: var(--accent); }
</style>
</head>
<body>

<header class="hero">
  <div class="hero-art" role="img" aria-label="Illustration of an astronaut floating above a planet"></div>
  <div class="hero-watermark">NOVALINE</div>
  <nav class="site-nav">
    <div class="brand"><span class="brand-dot"></span>NOVALINE</div>
    <ul class="nav-links">
      <li class="is-active">Home</li><li>About Us</li><li>Services</li><li>Pricing</li><li>Contact Us</li><li>Sign Up</li>
    </ul>
  </nav>
  <div class="hero-copy">
    <h1 class="hero-title">Novaline Is An Omnichannel</h1>
    <p class="hero-sub">Provider For Customer Care</p>
    <div class="hero-actions"><a href="#">Learn More</a><a href="#">Get Quote</a></div>
  </div>
  <svg class="hero-wave" viewBox="0 0 769 120" preserveAspectRatio="none">
    <path d="M0 60 C 200 130, 480 20, 769 40 L769 120 L0 120 Z" fill="#ffffff"/>
  </svg>
</header>

<section class="services">
  <article class="service-card card-digital">
    <div class="icon-box">
      <svg width="30" height="24" viewBox="0 0 30 24" fill="none" stroke="#ffffff" stroke-width="1.6"><rect x="2" y="2" width="26" height="16" rx="1"/><path d="M10 22h10M15 18v4"/></svg>
    </div>
    <h3>Digital Services</h3>
    <p>Chat and Email Care</p>
  </article>
  <article class="service-card card-call alt">
    <div class="icon-box">
      <svg width="26" height="26" viewBox="0 0 26 26" fill="none" stroke="#1f7390" stroke-width="1.6"><path d="M5 14a8 8 0 0 1 16 0"/><rect x="3" y="14" width="4" height="7" rx="1"/><rect x="19" y="14" width="4" height="7" rx="1"/></svg>
    </div>
    <h3>Call Center Services</h3>
    <p>Inbound and Outbound Calls</p>
  </article>
  <div class="what-we-do">
    <h2>What We Do</h2>
    <p>Novaline is a playful call center partner for online stores. We answer calls, chats and emails, run outbound campaigns and keep every shopper happy, so you can focus on growing your brand while we handle the rest.</p>
    <span class="btn-more">More</span>
  </div>
</section>

<section class="faq">
  <h2>Frequently Asked Questions</h2>
  <div class="faq-rule"></div>
  <p class="faq-sub">Quick answers to the questions our clients ask most often</p>
  <div class="faq-slider">
    <p class="faq-answer">Yes. The free trial gives you full access to our call and chat team for fourteen days, with no card needed and no contract to sign when it ends.</p>
    <p class="faq-question">Is the free trial really free?</p>
    <div class="faq-brand"><span class="brand-dot"></span>NOVALINE</div>
  </div>
  <svg class="faq-arrow prev" viewBox="0 0 16 10" fill="none" stroke="#14506b" stroke-width="1.4"><path d="M15 5H2M6 1L2 5l4 4"/></svg>
  <div class="faq-dots"><span class="is-active"></span><span></span><span></span><span></span><span></span></div>
  <svg class="faq-arrow next" viewBox="0 0 16 10" fill="none" stroke="#14506b" stroke-width="1.4"><path d="M1 5h13M10 1l4 4-4 4"/></svg>
  <div class="rocket-art" role="img" aria-label="Illustration of a rocket launching"></div>
</section>

<section class="callback">
  <aside class="contact-box">
    <h3>Contact Details</h3>
    <ul>
      <li><svg width="9" height="9" viewBox="0 0 10 10" fill="#ffffff"><path d="M2 1l2 2-1 1.5a6 6 0 0 0 2.5 2.5L7 6l2 2-1 1.5C4 9 1 6 .5 2z"/></svg>+1 (555) 014-2288</li>
      <li><svg width="9" height="9" viewBox="0 0 10 10" fill="none" stroke="#ffffff"><rect x="1" y="2" width="8" height="6"/><path d="M1 2l4 3 4-3"/></svg>hello@novaline.com</li>
      <li><svg width="9" height="9" viewBox="0 0 10 10" fill="#ffffff"><path d="M5 0a3.5 3.5 0 0 0-3.5 3.5C1.5 6 5 10 5 10s3.5-4 3.5-6.5A3.5 3.5 0 0 0 5 0z"/></svg>220 Orbit Lane, Suite 4, Denver</li>
    </ul>
  </aside>
  <form class="callback-form">
    <h2>Request For Call Back</h2>
    <div class="field-grid">
      <div class="field">Name</div><div class="field">Email</div>
      <div class="field">Phone</div><div class="field">Company</div>
    </div>
    <span class="btn-submit">Submit Now</span>
  </form>
</section>

<footer class="site-footer">
  <p>Copyright © 2024 Novaline. All rights reserved.</p>
  <ul class="footer-links">
    <li class="is-active">Home</li><li>About</li><li>Services</li><li>Pricing</li><li>Contact</li><li>Account</li>
  </ul>
</footer>

</body>
</html>
```